Thornbury Building Company - Card Design

I am looking to use the logo designs that you already did for me to develop a business card. I would like the card to have a black background and be double sided. I want white and green logo and text. I have attached an inspiration photo of a look that I like. I would like to use the Vertical Logo attached to take up the full front side of the card. On the back where I have my name and information, I would like to have the horizontal logo or maybe even just the image of the 'A' and trees without the text. I am open, but I am looking for something clean and simple and I want the green to really pop! Additional files can be found under Design #: 58302946

Target Market(s)

Homeowners

Industry/Entity Type

Construction

Contact Information for Business Card

Name: Marcus Thornbury, Title: Project Manager, Phone: 555.274.8136, Email: thornburybuildingcompany@mailvesta.com, address: 487 Larkspur Ln, Felton, CA 95033, Lic# 2468317

Colors
00AB8E
00BBA5
67D7C9
C6EFE9
E9F9F6

Requirements
Nice to have
• I would like to see the logos that I have already got from ArtLoomHub, though I am open to new ones

```html
<!DOCTYPE html>
<html lang="en">
<head>
<meta charset="utf-8">
<title>Thornbury Building Company – Business Card</title>
<link href="https://fonts.googleapis.com/css2?family=Open+Sans:wght@400;600;700&display=swap" rel="stylesheet">
<style>
  :root {
    --backdrop: #4a4a4a;
    --card-black: #161616;
    --card-edge: #3cbf4a;
    --band-green: #72b84a;
    --accent-green: #6cb843;
    --back-green: #39b54a;
    --back-green-deep: #2fa23f;
    --text-white: #ffffff;
  }
  * { box-sizing: border-box; margin: 0; padding: 0; }
  html, body {
    width: 1200px; height: 801px; overflow: hidden;
    background: var(--backdrop);
    font-family: "Open Sans", Arial, sans-serif;
  }
  .stage {
    position: relative; width: 1200px; height: 801px;
    display: flex; align-items: center; justify-content: center; gap: 40px;
  }
  .card {
    position: relative; width: 540px; height: 309px;
    border: 2px solid var(--card-edge);
    overflow: hidden;
  }
  /* Front */
  .card--front { background: var(--card-black); }
  .brand {
    position: absolute; left: 34px; top: 104px; width: 170px;
    display: flex; align-items: center; gap: 10px;
  }
  .brand__mark {
    flex: none; width: 30px; height: 30px; border-radius: 50%;
    background: var(--accent-green);
  }
  .brand__name {
    color: var(--text-white); font-weight: 600; font-size: 17px; line-height: 1.2;
  }
  .divider {
    position: absolute; left: 218px; top: 62px; width: 2px; height: 148px;
    background: var(--accent-green);
  }
  .divider::before {
    content: ""; position: absolute; left: 0; top: 0; width: 22px; height: 2px;
    background: var(--accent-green);
  }
  .details { position: absolute; left: 238px; top: 58px; right: 14px; }
  .details__name {
    color: var(--accent-green); font-weight: 700; font-size: 23px; line-height: 1.15;
  }
  .details__title {
    color: var(--text-white); font-size: 14px; margin-bottom: 14px;
  }
  .contact-list { list-style: none; }
  .contact-list li {
    display: flex; align-items: center; gap: 7px;
    color: var(--text-white); font-size: 12px; line-height: 21px; white-space: nowrap;
  }
  .contact-list svg { flex: none; width: 12px; height: 12px; fill: var(--accent-green); }
  .license-band {
    position: absolute; left: 0; right: 0; bottom: 38px; height: 28px;
    background: var(--band-green);
    display: flex; align-items: center; padding-left: 238px;
    color: var(--text-white); font-size: 14px;
  }
  /* Back */
  .card--back {
    background: linear-gradient(135deg, var(--back-green) 0%, var(--back-green-deep) 100%);
  }
  .logo-pattern { position: absolute; inset: 0; }
</style>
</head>
<body>
<main class="stage">
  <section class="card card--front" aria-label="Business card front">
    <div class="brand">
      <span class="brand__mark"></span>
      <span class="brand__name">Thornbury Building Company</span>
    </div>
    <div class="divider"></div>
    <div class="details">
      <p class="details__name">Marcus Thornbury</p>
      <p class="details__title">Project Manager</p>
      <ul class="contact-list">
        <li>
          <svg viewBox="0 0 24 24" aria-hidden="true"><path d="M6.6 10.8a15.1 15.1 0 0 0 6.6 6.6l2.2-2.2a1 1 0 0 1 1-.25 11.4 11.4 0 0 0 3.6.57 1 1 0 0 1 1 1V20a1 1 0 0 1-1 1A17 17 0 0 1 3 4a1 1 0 0 1 1-1h3.5a1 1 0 0 1 1 1c0 1.25.2 2.45.57 3.57a1 1 0 0 1-.25 1z"/></svg>
          555.274.8136
        </li>
        <li>
          <svg viewBox="0 0 24 24" aria-hidden="true"><path d="M2 5h20v14H2z M2 5l10 8 10-8" /></svg>
          thornburybuildingcompany@mailvesta.com
        </li>
        <li>
          <svg viewBox="0 0 24 24" aria-hidden="true"><path d="M12 2a7 7 0 0 0-7 7c0 5.25 7 13 7 13s7-7.75 7-13a7 7 0 0 0-7-7zm0 9.5a2.5 2.5 0 1 1 0-5 2.5 2.5 0 0 1 0 5z"/></svg>
          487 Larkspur Ln, Felton, CA 95033
        </li>
      </ul>
    </div>
    <div class="license-band">License# 2468317</div>
  </section>

  <section class="card card--back" aria-label="Business card back">
    <div class="logo-pattern" role="img" aria-label="Repeating tone-on-tone embossed company logo pattern across green background"></div>
  </section>
</main>
</body>
</html>
```